New web design for a service provider in the medical field

We are looking for a new design for our website. We are a company that repairs and sells medical endoscopes. Our customers include doctors and hospitals. Our current website can be found at https://lumavex.de/en/lumavex-english.
We need a new web design (without programming) for the following 3 pages:
-Startpage https://lumavex.de/en/lumavex-english/
-Used endoscopes https://lumavex.de/en/used-endoscopes/
-Purchase https://lumavex.de/en/purchase/
The design should be modern and stylish.
The blue color of the logo should be reflected on the page, but not too intrusive.
I have uploaded the images from the header. If more images are needed, let me know and I will upload them.

Target Market(s)
Doctors and hospitals

```html
<!DOCTYPE html>
<html lang="en">
<head>
<meta charset="utf-8">
<title>Lumavex – Endoscope Repair and Sales</title>
<link href="https://fonts.googleapis.com/css2?family=Roboto:wght@400;500;700;900&display=swap" rel="stylesheet">
<style>
:root{
  --navy:#14283d;
  --navy-deep:#0f2134;
  --blue:#1f8fd8;
  --blue-dark:#1670b3;
  --ink:#1c2b3a;
  --text:#5d6672;
  --soft:#eef4f9;
  --white:#fff;
}
*{margin:0;padding:0;box-sizing:border-box}
html,body{width:1200px;height:4360px;overflow:hidden}
body{font-family:'Roboto',Arial,sans-serif;color:var(--ink);background:var(--white);position:relative}
.abs{position:absolute}
.btn{position:absolute;display:flex;align-items:center;justify-content:center;border-radius:0 22px 22px 22px;font-weight:700;font-size:13px;letter-spacing:.2px;text-transform:uppercase}
.btn.blue{background:var(--blue);color:#fff}
.btn.dark{background:var(--navy);color:#fff}
.btn.white{background:#fff;color:var(--ink)}

/* top bar */
.topbar{left:0;top:0;width:1200px;height:90px;background:var(--navy)}
.circ{position:absolute;border-radius:50%;background:var(--blue);display:flex;align-items:center;justify-content:center}
.topbar .info{position:absolute;top:14px;color:#fff;font-size:14px}
.social{position:absolute;width:30px;height:30px;border-radius:50%;background:var(--blue);border:2px solid #fff}
.social.outline{background:transparent}

/* nav */
.nav{left:73px;top:47px;width:1053px;height:84px;background:#fff;border-radius:42px;box-shadow:0 6px 20px rgba(0,0,0,.12);z-index:5}
.brand{position:absolute;left:46px;top:28px;font-size:22px;font-weight:700;color:var(--ink);display:flex;align-items:center;gap:8px}
.brand i{display:block;width:14px;height:14px;border-radius:50%;background:var(--blue)}
.nav a{position:absolute;top:33px;font-size:14px;font-weight:700;color:var(--ink);text-decoration:none;text-transform:uppercase}
.nav a.active{color:var(--blue);text-decoration:underline}

/* hero */
.hero-photo{left:0;top:0;width:1200px;height:710px;background:linear-gradient(120deg,#5f8fb0 0%,#9fbdd3 40%,#d6d9dc 65%,#b58a6a 85%,#8c6d58 100%)}
.hero-title{left:110px;top:308px;width:560px;color:#fff;font-size:34px;font-weight:900;line-height:44px;text-transform:uppercase}
.slider-pill{left:1041px;top:310px;width:46px;height:134px;background:var(--blue);border-radius:23px;color:#fff;font-size:12px;font-weight:700}
.slider-pill span{position:absolute;left:50%;transform:translateX(-50%) rotate(-90deg);white-space:nowrap}

/* about */
.about-bg{left:0;top:640px;width:1200px;height:647px;background:linear-gradient(180deg,#f2f7fb,#e9f1f7)}
h2.section{font-size:40px;font-weight:900;text-transform:uppercase;color:var(--ink)}
h2.section b{color:var(--blue);font-weight:900}
.about-text{left:112px;top:888px;width:490px;font-size:13px;line-height:25.6px;color:var(--text);text-align:justify}
.about-text strong{color:var(--ink)}
.about-arc{left:685px;top:745px;width:424px;height:424px;border-radius:50%;background:var(--blue)}
.about-photo{left:659px;top:760px;width:430px;height:430px;border-radius:50%;background:linear-gradient(150deg,#d9e2ea,#8ba6bf 55%,#3b5f8f);border:6px solid #fff}

/* what we do */
.card{position:absolute;top:1466px;width:308px;height:402px;background:#fff;border-radius:0 48px 0 48px;box-shadow:0 8px 24px rgba(20,40,61,.12);text-align:center}
.card.featured{border-bottom:5px solid var(--navy);box-shadow:0 10px 30px rgba(20,40,61,.22)}
.card .icon{position:absolute;left:107px;top:31px;width:94px;height:94px;border-radius:50%;background:var(--blue)}
.card h3{position:absolute;left:0;right:0;top:151px;font-size:18px;font-weight:700;text-transform:uppercase}
.card p{position:absolute;left:14px;right:14px;top:184px;font-size:12.5px;line-height:25px;color:var(--text)}
.card .btn{left:72px;top:327px;width:164px;height:42px;font-size:12px}

/* faulty band */
.faulty-photo{left:0;top:1981px;width:1200px;height:469px;background:linear-gradient(100deg,#2d5e88 0%,#5c8fb6 35%,#a8c4d8 60%,#d9e3ea 100%)}
.faulty-circle{left:711px;top:2028px;width:376px;height:376px;border-radius:50%;background:#fff;text-align:center}
.faulty-circle h3{margin-top:68px;font-size:31px;font-weight:900;line-height:40px;text-transform:uppercase}
.faulty-circle h3 b{color:var(--blue)}
.faulty-circle p{font-size:15px;color:var(--ink);margin-top:10px;line-height:34px}

/* decision */
.decision{left:0;top:2450px;width:1200px;height:555px;background:linear-gradient(180deg,var(--navy-deep),#193350)}
.decision h2{position:absolute;left:0;right:0;top:62px;text-align:center;color:#fff;font-size:26px;font-weight:700;line-height:36px;text-transform:uppercase}
.feature{position:absolute;top:159px;width:230px;height:315px;background:#fff;border-radius:4px;text-align:center}
.feature .ring{position:absolute;left:71px;top:21px;width:88px;height:88px;border-radius:50%;border:2px dashed var(--navy);padding:8px}
.feature .ring i{display:block;width:100%;height:100%;border-radius:50%;background:var(--blue)}
.feature h4{position:absolute;left:0;right:0;top:146px;font-size:15.5px;font-weight:700;text-transform:uppercase}
.feature p{position:absolute;left:12px;right:12px;top:178px;font-size:11.5px;line-height:22px;color:var(--text)}
.dots{position:absolute;left:565px;top:505px;display:flex;gap:12px}
.dots i{width:9px;height:9px;border-radius:50%;background:#5c6f84}
.dots i.on{background:#fff}

/* systems */
.sys-frame{left:112px;top:3098px;width:402px;height:436px;border:6px solid var(--blue);border-radius:18px 0 0 0}
.sys-photo{left:134px;top:3120px;width:403px;height:435px;border-radius:0 34px 0 34px;background:linear-gradient(135deg,#cfd6dc,#eef1f3 50%,#9aa6b2)}
.sys-text{left:599px;top:3210px;width:490px;font-size:13px;line-height:25.6px;color:var(--text);text-align:justify}
.sys-text p+p{margin-top:9px}

/* help */
.help{left:0;top:3665px;width:1200px;height:400px;background:linear-gradient(120deg,#2a92d6,#1a7bc4 55%,#1665a8)}
.help h2{position:absolute;left:0;right:0;top:62px;text-align:center;color:#fff;font-size:32px;font-weight:900;text-transform:uppercase}
.help p{position:absolute;left:160px;right:160px;top:117px;text-align:center;color:#fff;font-size:14px;line-height:26px}

/* footer */
.footer{left:0;top:4040px;width:1200px;height:320px;background:var(--navy)}
.f-brand{left:118px;top:4153px;color:#fff;font-size:28px;font-weight:700;display:flex;align-items:center;gap:10px}
.f-brand i{display:block;width:16px;height:16px;border-radius:50%;background:var(--blue)}
.f-col h5{color:#fff;font-size:15px;font-weight:700;text-transform:uppercase;margin-bottom:18px}
.f-col ul{list-style:none}
.f-col li{color:#fff;font-size:14px;height:30.5px;display:flex;align-items:flex-start;gap:14px}
.f-col li::before{content:"";width:12px;height:12px;margin-top:3px;border-radius:50%;background:var(--blue);box-shadow:inset 0 0 0 3px var(--blue),inset 0 0 0 5px #fff}
.contact-row{position:absolute;left:869px;display:flex;align-items:center;gap:20px;color:#fff;font-size:14px;line-height:22px}
.contact-row .circ{position:relative;width:40px;height:40px;background:#fff;flex:none}
.f-rule{left:112px;top:4305px;width:976px;height:1px;background:rgba(255,255,255,.18)}
.copy{left:0;right:0;top:4321px;text-align:center;color:#fff;font-size:13px}
</style>
</head>
<body>

<!-- top bar -->
<div class="abs topbar">
  <div class="circ" style="left:110px;top:7px;width:30px;height:30px">
    <svg width="14" height="14" viewBox="0 0 24 24"><path fill="#fff" d="M6.6 10.8a15.1 15.1 0 006.6 6.6l2.2-2.2c.3-.3.7-.4 1-.2 1.1.4 2.3.6 3.6.6.6 0 1 .4 1 1V20c0 .6-.4 1-1 1A17 17 0 013 4c0-.6.4-1 1-1h3.5c.6 0 1 .4 1 1 0 1.3.2 2.5.6 3.6.1.3 0 .7-.2 1z"/></svg>
  </div>
  <div class="info" style="left:152px">+49 4000 555 120-0</div>
  <div class="circ" style="left:312px;top:7px;width:30px;height:30px">
    <svg width="14" height="14" viewBox="0 0 24 24"><path fill="#fff" d="M2 5h20v14H2z"/><path fill="none" stroke="#1f8fd8" stroke-width="2" d="M2 5l10 8 10-8"/></svg>
  </div>
  <div class="info" style="left:352px">info@lumavex.de</div>
  <div class="social" style="left:979px;top:7px" aria-label="Social profile"></div>
  <div class="social outline" style="left:1018px;top:7px" aria-label="Social profile"></div>
  <div class="social outline" style="left:1057px;top:7px" aria-label="Social profile"></div>
</div>

<!-- hero -->
<div class="abs hero-photo" role="img" aria-label="Gloved hands holding an endoscope in a clinical setting"></div>
<svg class="abs" style="left:0;top:560px" width="1200" height="150" viewBox="0 0 1200 150">
  <path d="M0 90 C 150 30, 300 150, 550 120 S 950 40, 1200 85 L1200 150 L0 150Z" fill="#f2f7fb"/>
  <path d="M0 100 C 160 50, 300 160, 560 125 S 960 55, 1200 100" fill="none" stroke="var(--blue)" stroke-width="9"/>
  <path d="M0 90 C 150 30, 300 150, 550 120 S 950 40, 1200 85" fill="none" stroke="#fff" stroke-width="3"/>
</svg>

<nav class="abs nav">
  <div class="brand"><i></i>lumavex</div>
  <a class="active" style="left:291px">Home</a>
  <a style="left:369px">Used Endoscopes ⌄</a>
  <a style="left:562px">Endoscopy Accessories ⌄</a>
  <a style="left:809px">Purchase</a>
  <a style="left:924px">Contact Us</a>
</nav>

<h1 class="abs hero-title">Put your endoscope in reliable hands!</h1>
<div class="btn white" style="left:112px;top:423px;width:144px;height:49px">Get Started</div>
<div class="abs slider-pill">
  <span style="top:34px">NEXT</span>
  <span style="top:95px">PREV</span>
  <i style="position:absolute;left:10px;top:66px;width:26px;height:2px;background:#fff"></i>
</div>

<!-- about -->
<div class="abs about-bg"></div>
<svg class="abs" style="left:0;top:700px" width="1200" height="560" aria-hidden="true">
  <g fill="#c9dceb"><circle cx="423" cy="116" r="9"/><circle cx="935" cy="-8" r="8"/><circle cx="113" cy="505" r="6"/><circle cx="330" cy="452" r="5"/><circle cx="1190" cy="550" r="6"/><circle cx="80" cy="30" r="4"/></g>
</svg>
<h2 class="abs section" style="left:110px;top:818px">About <b>Us</b></h2>
<div class="abs about-text"><strong>Lumavex</strong> is a privileged partner for the start-up facility or optimisation of existing healthcare facilities, doctor's offices and hospitals. The quality and reliability of our products and our offered service are our best advertisement! As a result of optimised processes and highly qualified specialists in our company, we can work very quickly and with high quality for your benefit of least possible restrictions in your doctor's office or in your hospital.</div>
<div class="btn blue" style="left:112px;top:1072px;width:137px;height:50px">Learn More</div>
<div class="abs about-arc"></div>
<div class="abs about-photo" role="img" aria-label="Technician in blue gloves handling an endoscope at a processor unit"></div>

<!-- what we do -->
<h2 class="abs section" style="left:0;right:0;top:1368px;text-align:center">What <b>We Do</b></h2>
<div class="card" style="left:112px">
  <div class="icon"></div>
  <h3>Repair</h3>
  <p>Manufacturer-independent we repair and maintain endoscopes, individual components (e.g. processors or light sources), accessories and peripherals of the manufacturers Olvaris, Pentrix and Fujova.</p>
  <div class="btn dark">Repair Request</div>
</div>
<div class="card featured" style="left:445px">
  <div class="icon"></div>
  <h3>Sale Used Endoscopes</h3>
  <p>Our regular stock includes refurbished gastroscopes, coloscopes, bronchoscopes, cystoscopes and duodenoscopes from the well-known manufacturers Olvaris, Pentrix and Fujova.</p>
  <div class="btn blue">Purchase Request</div>
</div>
<div class="card" style="left:779px">
  <div class="icon"></div>
  <h3>Purchase</h3>
  <p>We are very interested in buying your old endoscopes – even defective and dismantled! We offer fair conditions! Please contact us for a purchase offer!</p>
  <div class="btn dark">Sell Device</div>
</div>

<!-- faulty -->
<div class="abs faulty-photo" role="img" aria-label="Gloved hands holding an endoscope control section"></div>
<div class="abs faulty-circle">
  <h3>Faulty<br><b>Endoscope?</b></h3>
  <p>We ensure quick and smooth repairs!<br>Simple place a</p>
  <div class="btn blue" style="left:111px;top:274px;width:154px;height:50px">Pick-Up Order</div>
</div>

<!-- decision -->
<section class="abs decision">
  <h2>Lumavex GmbH,<br>your decision for your future</h2>
  <div class="feature" style="left:112px"><div class="ring"><i></i></div><h4>Fast Repairs</h4><p>Keep potential disruptions in your doctor's office or in your hospital at minimum as a result of optimized processes and highly qualified specialists in our company</p></div>
  <div class="feature" style="left:361px"><div class="ring"><i></i></div><h4>Highly Cost Efficient</h4><p>Benefit from our first class recommendations &amp; implementation by our experienced staff. Our goals is to find the best solutions together with you at the best lowest price point.</p></div>
  <div class="feature" style="left:610px"><div class="ring"><i></i></div><h4>On-Site Service</h4><p>We will gladly pay you a visit to to carry out analysis and repairs on site. Due to our many years of experience – it doesn't get any faster (whigleithin a 250 km range)</p></div>
  <div class="feature" style="left:858px"><div class="ring"><i></i></div><h4>Loan Equipment Service</h4><p>Use our service of high-quality loan devices during the downtime of your defective endoscope (limited to stock)</p></div>
  <div class="dots"><i></i><i class="on"></i><i></i><i></i></div>
</section>

<!-- endoscopy systems -->
<div class="abs sys-frame"></div>
<div class="abs sys-photo" role="img" aria-label="Medical professional operating an endoscopy tower with monitor"></div>
<h2 class="abs section" style="left:598px;top:3140px;font-size:31px">Endoscopy <b>Systems</b></h2>
<div class="abs sys-text">
  <p>Endoscopy is one of the most important tools in the diagnostic assessment of medical problems. The cost-effective and efficient use of medical devices and the smooth flow of treatments are the goals when planning and setting up every new or redesigning an existing endoscopy department in medical doctor's offices and hospitals.</p>
  <p>.Professionally tested or repaired used devices are the perfect solution for those who are looking for a reliable but inexpensive alternative to new devices. We support you – with manufacturer-neutral advice</p>
</div>
<div class="btn blue" style="left:599px;top:3455px;width:137px;height:43px">Learn More</div>

<!-- help -->
<section class="abs help" role="img" aria-label="Blue tinted background of endoscopy equipment">
  <h2>How can we help you?</h2>
  <p>Good morning! We are looking forward to your message! You can get informations on possible or ongoing repairs of your endoscope technology. You can also get an advise on rational inspection intervals and in choosing the right accessories.</p>
  <div class="btn dark" style="left:518px;top:198px;width:163px;height:44px">Send Message</div>
</section>
<svg class="abs" style="left:0;top:3960px" width="1200" height="110" viewBox="0 0 1200 110">
  <path d="M0 40 C 200 110, 420 110, 620 70 S 1000 -10, 1200 40 L1200 110 L0 110Z" fill="var(--navy)"/>
  <path d="M0 40 C 200 110, 420 110, 620 70 S 1000 -10, 1200 40" fill="none" stroke="#fff" stroke-width="4"/>
</svg>

<!-- footer -->
<footer class="abs footer"></footer>
<div class="abs f-brand"><i></i>lumavex</div>
<div class="abs f-col" style="left:369px;top:4093px">
  <h5>Quick Links</h5>
  <ul><li>Home</li><li>Endoscope Services</li><li>Endoscope Accessories</li><li>Purchase</li><li>Contact Us</li></ul>
</div>
<div class="abs f-col" style="left:635px;top:4093px">
  <h5>Other Links</h5>
  <ul><li>FAQ</li><li>Blog</li><li>Privacy Policy</li><li>Terms &amp; Conditions</li></ul>
</div>
<div class="abs f-col" style="left:869px;top:4093px"><h5>Contact Info</h5></div>
<div class="contact-row" style="top:4140px"><span class="circ"><svg width="14" height="18" viewBox="0 0 24 30"><path fill="#1f8fd8" d="M12 0a10 10 0 00-10 10c0 7.5 10 20 10 20s10-12.5 10-20A10 10 0 0012 0zm0 14a4 4 0 110-8 4 4 0 010 8z"/></svg></span><span>Birkenallee 14, 21400<br>Nordheim, Germany</span></div>
<div class="contact-row" style="top:4202px"><span class="circ"><svg width="16" height="16" viewBox="0 0 24 24"><path fill="#1f8fd8" d="M6.6 10.8a15.1 15.1 0 006.6 6.6l2.2-2.2c.3-.3.7-.4 1-.2 1.1.4 2.3.6 3.6.6.6 0 1 .4 1 1V20c0 .6-.4 1-1 1A17 17 0 013 4c0-.6.4-1 1-1h3.5c.6 0 1 .4 1 1 0 1.3.2 2.5.6 3.6.1.3 0 .7-.2 1z"/></svg></span><span>+49 4000 555 120-0</span></div>
<div class="contact-row" style="top:4254px"><span class="circ"><svg width="16" height="14" viewBox="0 0 24 20"><path fill="#1f8fd8" d="M0 2h24v16H0z"/><path fill="none" stroke="#fff" stroke-width="2" d="M0 2l12 9 12-9"/></svg></span><span>info@lumavex.de</span></div>
<div class="abs f-rule"></div>
<div class="abs copy">© 2022 <strong>Lumavex</strong> &nbsp;|&nbsp; All Rights Reserved</div>
<div class="social" style="left:979px;top:4314px" aria-label="Social profile"></div>
<div class="social" style="left:1018px;top:4314px;background:var(--navy-deep)" aria-label="Social profile"></div>
<div class="social" style="left:1057px;top:4314px;background:var(--navy-deep)" aria-label="Social profile"></div>

</body>
</html>
```